Website for a company offering full serivce charging solutions for electric cars

The company "tanu-werk" (english: "tanu-works") offering all-in-one-solutions for charging infrastructure for electric mobility.

There are four products:
1- Wallboxes for single-family homes
2- Solutions for property devloper/-management for property parking space
3- All-in-one-charging solution for municipalities/communities
4- Solutions for tourism/hotels/holiday appartments

The Website structure:
1. Main Page
2.1. Product Page Single Homes
2.2. Product Page Property Management / Parking
2.3. Product Page Municipality
2.4. Product Page Tourism
3. Contact Form / Request for information
4. Imprint / Legal

The Website should be built on Wordpress with a powerful possibility to simply add/modify specific landing pages.

We would like you to implement the website later and also maintain it if possible, but we would be able to do minor modifications by ourselfs (for A/B-Testing)

The website should be clear and simple, easy to understand.
Target group is mainly B2C without deeper knowledge of that topic.

It should suggest, that we will provide a very simple way to get the charging infrastructure done.

We need a contact form, maybe we will use Hubspot later.

Attached you will find a draft of the main page and a landing page (for 2.2) - it is just the content, please ignore the design. We would love to let you create a suitable design.
Also you will find some drafts a bit different for the same story.

I added also a few stock photos, but they don't need to be used! If you have better ideas, you are welcome!

Industry/Entity Type

Charging/Electric mobility

Number of Pages Required

2 page

Font styles to use
Sans Serif

Requirements
Must have
• Based on Wordpress, and the designer should be able to implement it on Wordpress on a later step

```html
<!DOCTYPE html>
<html lang="de">
<head>
<meta charset="utf-8">
<title>tanu-werk – Ladelösungen für E-Mobilität</title>
<link href="https://fonts.googleapis.com/css2?family=Audiowide&family=Roboto:wght@400;500;700&display=swap" rel="stylesheet">
<style>
:root{
  --bg:#0e1322;
  --bg-deep:#0a0e1b;
  --bar:#161b2c;
  --pink:#e91e8c;
  --violet:#7b52c9;
  --lilac:#7a63d4;
  --text:#ffffff;
  --muted:#d9dbe3;
  --line:#2c3247;
}
*{box-sizing:border-box;margin:0;padding:0}
html,body{width:1200px;height:3682px;overflow:hidden}
body{background:var(--bg);color:var(--text);font-family:'Roboto',sans-serif;position:relative}
.abs{position:absolute}
.display{font-family:'Audiowide',sans-serif;font-weight:400}
.btn{position:absolute;display:flex;align-items:center;justify-content:center;gap:8px;border-radius:26px;background:linear-gradient(90deg,var(--pink),var(--violet));color:#fff;font-weight:700;font-size:16px;text-transform:uppercase;text-decoration:none}
.btn .dot{width:14px;height:14px;border-radius:50%;background:#fff;display:inline-flex;align-items:center;justify-content:center}
.brand{display:flex;align-items:center;gap:10px;color:#fff;font-family:'Roboto',sans-serif;font-weight:500}
.brand .mark{border-radius:50%;background:var(--pink)}

/* header */
.site-header{top:0;left:0;width:1200px;height:88px;background:var(--bar)}
.site-header .brand{position:absolute;left:110px;top:28px;font-size:26px}
.site-header .mark{width:30px;height:30px}
.nav{position:absolute;top:33px;left:409px;display:flex;gap:27px;font-size:15px;font-weight:500}
.nav a{color:#fff;text-decoration:none}
.nav a.active{color:var(--pink)}
.header-cta{left:872px;top:22px;width:215px;height:42px;font-size:15px;text-transform:none;font-weight:500}

/* hero */
.hero{top:88px;left:0;width:1200px;height:604px;background:linear-gradient(110deg,#2a2f44 0%,#4a5068 35%,#2b3250 60%,#18213f 80%,#14235a 100%)}
.hero-title{left:110px;top:264px;font-size:44px;line-height:50px}
.hero-text{left:110px;top:380px;font-size:17px;line-height:28px;font-weight:500;width:470px}
.hero .btn{left:110px;top:374px;width:211px;height:48px}
.arrow{position:absolute;top:283px;width:42px;height:42px;border-radius:50%;background:#111522;display:flex;align-items:center;justify-content:center}

/* about */
.about{top:692px;left:0;width:1200px;height:346px;background:var(--bg-deep);text-align:center}
.about .mark{position:absolute;left:588px;top:66px;width:24px;height:24px;border-radius:50%;background:var(--pink)}
.about h2{position:absolute;top:98px;width:100%;font-size:42px}
.about p{position:absolute;left:140px;width:920px;font-size:14px;line-height:25px;color:var(--muted)}

.offer-head{top:1104px;left:100px;width:1000px;text-align:center;font-size:34px;line-height:46px}

/* segments */
.ring{position:absolute;border-radius:50%;background:linear-gradient(160deg,var(--pink),var(--violet) 60%,var(--lilac))}
.photo{position:absolute;border-radius:50%}
.seg-title{font-size:38px;color:var(--lilac)}
.ticks{list-style:none;font-size:14px;line-height:23px;color:var(--muted)}
.ticks li{position:relative;padding-left:31px;margin-bottom:9px}
.ticks li::before{content:"";position:absolute;left:0;top:5px;width:12px;height:12px;border-radius:50%;background:var(--pink)}
.ticks li::after{content:"";position:absolute;left:3px;top:8px;width:5px;height:3px;border-left:1.5px solid #fff;border-bottom:1.5px solid #fff;transform:rotate(-45deg)}
.sub{list-style:none;margin:14px 0 6px}
.sub li{padding-left:23px;margin-bottom:3px}
.sub li::before{left:0;top:6px;width:11px;height:11px;background:var(--violet)}
.sub li::after{display:none}
.seg .btn{width:183px;height:48px}

/* footer */
.site-footer{top:3336px;left:0;width:1200px;height:346px;background:var(--bar)}
.site-footer .brand{position:absolute;left:110px;top:148px;font-size:36px}
.site-footer .mark{width:34px;height:34px}
.fcol{position:absolute;top:50px}
.fcol h4{font-size:16px;font-weight:700;margin-bottom:20px}
.contact-item{position:relative;padding-left:24px;margin-bottom:14px;font-size:13px;line-height:18px}
.contact-item b{display:block;font-size:12px}
.contact-item svg{position:absolute;left:0;top:2px}
.links a{display:block;color:#fff;text-decoration:none;font-size:13px;line-height:26px}
.subscribe{position:absolute;left:792px;top:98px;width:296px;height:44px;border-radius:22px;background:#fff}
.subscribe span{position:absolute;left:22px;top:15px;font-size:11px;color:#888}
.subscribe b{position:absolute;right:0;top:0;width:122px;height:44px;border-radius:22px;background:linear-gradient(90deg,var(--pink),var(--violet));display:flex;align-items:center;justify-content:center;font-size:16px}
.social{position:absolute;top:216px;display:flex;gap:12px;left:787px}
.social i{width:31px;height:31px;border-radius:50%;border:1.5px solid #fff;display:block}
.footer-line{left:110px;top:266px;width:980px;height:1px;background:var(--line)}
.go-up{left:1008px;top:257px;width:82px;height:20px;border-radius:10px;background:#fff;color:#161b2c;font-size:11px;font-weight:700;display:flex;align-items:center;justify-content:center}
.legal{top:303px;font-size:13px}
</style>
</head>
<body>

<header class="abs site-header">
  <div class="brand"><span class="mark"></span>tanu-werk.de</div>
  <nav class="nav">
    <a class="active" href="#">Lösungen</a><a href="#">Unternehmen</a><a href="#">Services</a><a href="#">Karriere</a><a href="#">Kontakt</a>
  </nav>
  <a class="btn header-cta" href="#">Ein Angebot bekommen</a>
</header>

<section class="abs hero" role="img" aria-label="Foto: Ladestecker steckt in einer Ladesäule für Elektroautos">
  <h1 class="abs display hero-title" style="top:176px">tanu-werk ist Ihr<br>Partner</h1>
  <p class="abs hero-text" style="top:292px">wenn das Laden nicht nur einfach, sondern die Umsetzung auch aus einer Hand kommen soll</p>
  <a class="btn" href="#">Get Started <span class="dot"><svg width="8" height="8" viewBox="0 0 8 8"><path d="M2 1l3 3-3 3" stroke="#e91e8c" stroke-width="1.6" fill="none"/></svg></span></a>
  <span class="arrow" style="left:35px"><svg width="14" height="18" viewBox="0 0 14 18"><path d="M10 2L3 9l7 7" stroke="#fff" stroke-width="2" fill="none"/></svg></span>
  <span class="arrow" style="left:1123px"><svg width="14" height="18" viewBox="0 0 14 18"><path d="M4 2l7 7-7 7" stroke="#fff" stroke-width="2" fill="none"/></svg></span>
</section>

<section class="abs about">
  <span class="mark"></span>
  <h2 class="display">Über Uns</h2>
  <p style="top:160px">Wir bieten Lösungen sowohl für Privatkunden, Geschäftskunden als auch Kommunen an, die schnell, fair und ohne Eigenleistung zu einer smarten Ladelösung für E-Fahrzeuge kommen möchten.</p>
  <p style="top:220px">Von der Beratung, über die Installation, Inbetriebnahme bis zur Abrechnung und Wartung bekommen Sie bei tanu-werk alles aus einer Hand. Auf Wunsch vermieten wir auch die Ladetechnik und übernehmen im gewerblichen Bereich die direkte Abrechnung mit dem Nutzer. Für Kommunen bieten wir den kostenfreien Full-Service an und beteiligen die Gemeinden an der Nutzung der Infrastruktur.</p>
</section>

<h2 class="abs display offer-head">Fragen Sie uns nach der auf Ihre individuellen Bedürfnisse zugeschnittenen Lösung:</h2>

<!-- Privatkunde -->
<section class="seg">
  <div class="ring" style="left:-80px;top:1236px;width:640px;height:640px"></div>
  <div class="photo" role="img" aria-label="Foto: Ladestecker an einem weißen Elektroauto mit blau leuchtendem Ladering" style="left:-84px;top:1256px;width:634px;height:624px;background:radial-gradient(circle at 65% 50%,#3a7bff 0%,#6fa0e0 25%,#b8c8de 55%,#2a3550 100%)"></div>
  <h3 class="abs display seg-title" style="left:633px;top:1334px">Als Privatkunde</h3>
  <ul class="abs ticks" style="left:633px;top:1408px;width:440px">
    <li>Bestandsanalyse mit umfangreicher Beratung über die Möglichkeiten der Umsetzung</li>
    <li>Prüfung und Übernahme der Anmeldung verfügbarer Fördermöglichkeiten Auswahl an smarten Wallbox Lösungen, passend für Ihr Fahrzeug und Ihre Bedürfnisse</li>
    <li>Installation inkl. aller notwendigen Materialien und Tätigkeiten (Durchbrüche, Erdarbeiten, etc.)</li>
    <li>Inbetriebnahme und Einweisung in die Ladetechnik</li>
    <li>Jährlich technische Wartung nach DGUV3</li>
    <li>Reparaturservice, unter Berücksichtigung der geltenden Garantie Ansprüche</li>
  </ul>
  <a class="btn" href="#" style="left:633px;top:1743px">Learn More <span class="dot"><svg width="8" height="8" viewBox="0 0 8 8"><path d="M2 1l3 3-3 3" stroke="#e91e8c" stroke-width="1.6" fill="none"/></svg></span></a>
</section>

<!-- Geschäftskunde -->
<section class="seg">
  <div class="ring" style="left:643px;top:1910px;width:650px;height:650px"></div>
  <div class="photo" role="img" aria-label="Foto: Nahaufnahme eines weißen Ladesteckers mit blau leuchtender Buchse" style="left:650px;top:1932px;width:640px;height:628px;background:radial-gradient(circle at 55% 45%,#7a8a9c 0%,#2c5cff 28%,#a9b8e8 50%,#e6e8ee 75%,#c9ccd6 100%)"></div>
  <h3 class="abs display seg-title" style="left:113px;top:1964px">Als Geschäftskunde</h3>
  <ul class="abs ticks" style="left:113px;top:2038px;width:480px">
    <li>Durchführung einer individuellen Bedarfsanalyse inkl. Ermittlung der Anforderungen für:
      <ul class="ticks sub">
        <li>Haus- und Immobilienverwaltungen</li>
        <li>Dienstleistungs- und Handelsunternehmen</li>
        <li>Hotel und Beherbergungsbetriebe</li>
        <li>Parkraum- und Parkhausbetreiber</li>
        <li>Tourismus, Sport- und Freizeiteinrichtungen</li>
      </ul>
    </li>
    <li>Planung und Projektierung des Installationsaufwands inkl. Materialverbrauch</li>
    <li>Leasing oder Kauf der Hardware</li>
    <li>Normgerechte Installation der Ladeinfrastruktur inkl. Durchbruch-, Brandschutz- und Erdarbeiten</li>
    <li>Bei Bestandsbauten Integration der Ladeinfrastruktur in die Gebäudesystemtechnik und ggf. Anpassung des Netzanschlusses</li>
  </ul>
  <a class="btn" href="#" style="left:113px;top:2468px">Learn More <span class="dot"><svg width="8" height="8" viewBox="0 0 8 8"><path d="M2 1l3 3-3 3" stroke="#e91e8c" stroke-width="1.6" fill="none"/></svg></span></a>
</section>

<!-- Kommune -->
<section class="seg">
  <div class="ring" style="left:-80px;top:2600px;width:645px;height:645px"></div>
  <div class="photo" role="img" aria-label="Foto: Ladekabel steckt in der Ladebuchse eines hellen Elektroautos" style="left:-86px;top:2620px;width:636px;height:624px;background:radial-gradient(circle at 40% 50%,#f0a080 0%,#5a6e96 20%,#b8c4da 50%,#e8ecf2 80%,#cfd6e2 100%)"></div>
  <h3 class="abs display seg-title" style="left:633px;top:2720px">Als Kommune</h3>
  <ul class="abs ticks" style="left:633px;top:2794px;width:460px">
    <li>Konzeptionierung möglicher Ladeinfrastrukturen innerhalb Ihrer Gemeinde</li>
    <li>Planung und Projektsteuerung inkl. sämtlicher behördlicher Genehmigungsverfahren und Beantragung von Fördermitteln</li>
    <li>Fachgerechte Installation und Inbetriebnahme</li>
    <li>Regelmäßige Wartung gemäß Vorschrif</li>
    <li>Reparatur und Kundenservice</li>
    <li>Direkte Abrechnung mit dem Nutzer</li>
    <li>Beteiligung der Gemeinde am Umsatz</li>
  </ul>
  <a class="btn" href="#" style="left:633px;top:3085px">Learn More <span class="dot"><svg width="8" height="8" viewBox="0 0 8 8"><path d="M2 1l3 3-3 3" stroke="#e91e8c" stroke-width="1.6" fill="none"/></svg></span></a>
</section>

<footer class="abs site-footer">
  <div class="brand"><span class="mark"></span>tanu-werk.de</div>
  <div class="fcol" style="left:377px">
    <h4>Unsere Büroadresse</h4>
    <div class="contact-item"><svg width="12" height="12" viewBox="0 0 12 12"><path d="M2 1h3l1 3-2 1a7 7 0 003 3l1-2 3 1v3c-6 1-10-3-9-9z" fill="#e91e8c"/></svg><b>Telefon</b>030 555 0142</div>
    <div class="contact-item"><svg width="13" height="10" viewBox="0 0 13 10"><rect width="13" height="10" rx="1" fill="#e91e8c"/><path d="M1 1l5.5 4.5L12 1" stroke="#161b2c" fill="none"/></svg><b>Email</b>kontakt@tanu-werk.example</div>
    <div class="contact-item"><svg width="10" height="13" viewBox="0 0 10 13"><path d="M5 0a5 5 0 00-5 5c0 4 5 8 5 8s5-4 5-8a5 5 0 00-5-5z" fill="#e91e8c"/><circle cx="5" cy="5" r="2" fill="#161b2c"/></svg><b>Location</b>123, Lorem ipsum dolor sit amet,<br>consectetur adipiscing elit</div>
  </div>
  <div class="fcol links" style="left:641px">
    <h4>Gesellschaft</h4>
    <a href="#">Lösungen</a><a href="#">Unternehmen</a><a href="#">Services</a><a href="#">Karriere</a><a href="#">Kontakt</a>
  </div>
  <div class="fcol" style="left:787px"><h4 style="font-size:18px">Abonnieren Sie Updates</h4></div>
  <div class="subscribe"><span>Emaill Address</span><b>SUBMIT</b></div>
  <div class="abs" style="left:788px;top:169px;font-size:13px;font-weight:500;display:flex;gap:8px;align-items:center"><svg width="12" height="12" viewBox="0 0 12 12"><rect x="1" y="1" width="10" height="10" rx="1" stroke="#fff" fill="none"/><path d="M3 6l2 2 4-5" stroke="#fff" stroke-width="1.5" fill="none"/></svg>Ja, bitte kontaktieren Sie mich.</div>
  <div class="social"><i></i><i></i><i></i></div>
  <div class="abs footer-line"></div>
  <div class="abs go-up">↑ Go Up</div>
  <div class="abs legal" style="left:112px">© 2022 tanu-werk | All Rights Reserved</div>
  <div class="abs legal" style="left:660px;word-spacing:2px">Datenschutzrichtlinie &nbsp;|&nbsp; Cookie-Richtlinie &nbsp;|&nbsp; Nutzungsbedingungen</div>
</footer>

</body>
</html>
```